wealth management firm, professional group, new model

we have a logo that works but we need a card, white background using our colors...clean look

our tag line if can be used in

The Bridge From Client to Owner

```html
<!DOCTYPE html>
<html lang="en">
<head>
<meta charset="utf-8">
<title>Varela Wealth Partners – Business Card</title>
<link href="https://fonts.googleapis.com/css2?family=Open+Sans:wght@400;700&display=swap" rel="stylesheet">
<style>
  :root {
    --navy: #162d52;
    --white: #ffffff;
    --rule-grey: #5a5a5a;
    --text-dark: #222222;
    --canvas-bg: #dcdcdc;
  }
  * { margin: 0; padding: 0; box-sizing: border-box; }
  html, body {
    width: 1200px; height: 1018px; overflow: hidden;
    background: var(--canvas-bg);
    font-family: "Open Sans", Arial, sans-serif;
  }
  .card {
    position: absolute;
    left: 220px;
    width: 760px; height: 434px;
    overflow: hidden;
    box-shadow: 0 6px 18px rgba(0,0,0,0.18);
  }
  .card--front { top: 30px; background: var(--white); }
  .card--back  { top: 554px; background: var(--navy); }

  /* front: name block */
  .name-tab {
    position: absolute; left: 0; top: 34px;
    width: 14px; height: 42px;
    background: var(--navy);
    border-radius: 0 5px 5px 0;
  }
  .holder-name {
    position: absolute; left: 30px; top: 28px;
    font-size: 32px; font-weight: 700; color: var(--navy);
    letter-spacing: 0.5px; line-height: 1.1;
  }
  .holder-role {
    position: absolute; left: 30px; top: 68px;
    font-size: 16px; font-weight: 400; color: var(--text-dark);
  }

  /* brand name placeholder */
  .brand {
    position: absolute;
    display: flex; align-items: center; gap: 12px;
  }
  .brand__dot { border-radius: 50%; flex: none; }
  .brand__name {
    font-weight: 400; line-height: 1.1; white-space: nowrap;
  }
  .tagline {
    position: absolute;
    font-weight: 400; white-space: nowrap;
  }

  .card--front .brand { right: 40px; top: 150px; }
  .card--front .brand__dot { width: 22px; height: 22px; background: var(--navy); }
  .card--front .brand__name { font-size: 34px; color: var(--navy); }
  .card--front .tagline {
    right: 40px; top: 204px;
    font-size: 16px; color: var(--text-dark);
  }

  .card--back .brand {
    left: 50%; top: 186px; transform: translateX(-50%);
  }
  .card--back .brand__dot { width: 28px; height: 28px; background: var(--white); }
  .card--back .brand__name { font-size: 44px; color: var(--white); }
  .card--back .tagline {
    left: 0; right: 0; top: 254px; text-align: center;
    font-size: 20px; color: var(--white);
  }

  /* divider + band */
  .divider {
    position: absolute; left: 0; right: 0; top: 250px;
    height: 5px; background: var(--rule-grey);
  }
  .contact-band {
    position: absolute; left: 0; right: 0; top: 262px; bottom: 0;
    background: var(--navy);
    color: var(--white);
  }
  .contact-list {
    list-style: none;
    position: absolute; left: 26px; top: 14px;
    font-size: 16px; line-height: 24px;
  }
  .contact-list li { display: flex; align-items: center; gap: 8px; }
  .contact-list svg { width: 12px; height: 12px; flex: none; }
  .address {
    position: absolute; right: 36px; bottom: 22px;
    text-align: right;
    font-size: 22px; line-height: 28px;
  }
</style>
</head>
<body>

<section class="card card--front" aria-label="Business card, front">
  <div class="name-tab"></div>
  <h1 class="holder-name">DANIEL HART</h1>
  <p class="holder-role">Manager</p>

  <div class="brand">
    <span class="brand__dot"></span>
    <span class="brand__name">Varela Wealth Partners</span>
  </div>
  <p class="tagline">The Bridge From Client to Owner</p>

  <div class="divider"></div>

  <div class="contact-band">
    <ul class="contact-list">
      <li>
        <svg viewBox="0 0 12 12" aria-hidden="true"><circle cx="6" cy="6" r="6" fill="#fff"/><path d="M4 3.2l1.2 1.3-.7.8c.4.9 1 1.5 1.9 1.9l.8-.7 1.3 1.2-.8 1c-2.3-.3-4.3-2.3-4.6-4.6z" fill="#162d52"/></svg>
        +012 345 6789
      </li>
      <li>
        <svg viewBox="0 0 12 12" aria-hidden="true"><circle cx="6" cy="6" r="6" fill="#fff"/><path d="M4 3.2l1.2 1.3-.7.8c.4.9 1 1.5 1.9 1.9l.8-.7 1.3 1.2-.8 1c-2.3-.3-4.3-2.3-4.6-4.6z" fill="#162d52"/></svg>
        +012 345 67890
      </li>
      <li>
        <svg viewBox="0 0 12 12" aria-hidden="true"><rect x="0.5" y="2.5" width="11" height="7" fill="#fff"/><path d="M0.5 2.5L6 6.5l5.5-4" fill="none" stroke="#162d52" stroke-width="1"/></svg>
        info@youremail.com
      </li>
      <li>
        <svg viewBox="0 0 12 12" aria-hidden="true"><circle cx="6" cy="6" r="5.5" fill="#fff"/><path d="M0.5 6h11M6 0.5c-2 2-2 9 0 11M6 0.5c2 2 2 9 0 11" fill="none" stroke="#162d52" stroke-width="0.8"/></svg>
        www.yourwebsite.com
      </li>
    </ul>
    <p class="address">Your loaction street here,<br>Your country name - 9120</p>
  </div>
</section>

<section class="card card--back" aria-label="Business card, back">
  <div class="brand">
    <span class="brand__dot"></span>
    <span class="brand__name">Varela Wealth Partners</span>
  </div>
  <p class="tagline">The Bridge From Client to Owner</p>
</section>

</body>
</html>
```